Great American Thank You

A 3in by 5in Thank You card design for a company that sells political humor greeting cards online. The specifications are as follows:

Front Text: Thank You For Being A Great American
Front Art: Cartoon eagle with American flag vest, screeching, holding a constitution (serif font)

No other art is required because the inside of the card will be blank.

```html
<!DOCTYPE html>
<html lang="en">
<head>
<meta charset="utf-8">
<title>Great American Thank You Card</title>
<link rel="stylesheet" href="https://fonts.googleapis.com/css2?family=Cinzel:wght@400;500&display=swap">
<style>
  :root {
    --navy-light: #0f3f82;
    --navy-dark: #072a5c;
    --white: #ffffff;
    --flag-red: #e8444a;
    --feather-dark: #141414;
    --feather-mid: #3a3a3a;
  }
  html, body {
    margin: 0;
    padding: 0;
    width: 1200px;
    height: 850px;
    overflow: hidden;
    background: var(--navy-dark);
  }
  .card {
    position: relative;
    width: 1200px;
    height: 850px;
    overflow: hidden;
    background: linear-gradient(90deg, var(--navy-light) 0%, var(--navy-dark) 70%);
    font-family: "Cinzel", "Times New Roman", serif;
    color: var(--white);
  }
  .card-art {
    position: absolute;
    inset: 0;
  }
  .greeting {
    position: absolute;
    left: 90px;
    margin: 0;
    font-weight: 400;
    line-height: 1;
    white-space: nowrap;
  }
  .greeting--thanks { top: 124px; font-size: 98px; }
  .greeting--for { top: 330px; font-size: 83px; }
  .greeting--great { top: 432px; font-size: 115px; font-weight: 500; }
  .greeting--american { top: 560px; font-size: 115px; font-weight: 500; }
  .star-row {
    position: absolute;
    left: 90px;
    display: flex;
    gap: 22px;
  }
  .star-row--top { top: 250px; }
  .star-row--bottom { top: 716px; }
  .star-row svg { width: 36px; height: 36px; fill: var(--white); }
</style>
</head>
<body>
<main class="card">
  <svg class="card-art" viewBox="0 0 1200 850" xmlns="http://www.w3.org/2000/svg">
    <defs>
      <linearGradient id="eagleTone" x1="0" y1="0" x2="1" y2="1">
        <stop offset="0" stop-color="var(--feather-mid)"/>
        <stop offset="1" stop-color="var(--feather-dark)"/>
      </linearGradient>
    </defs>
    <rect class="frame" x="20" y="20" width="1300" height="803" fill="none" stroke="var(--white)" stroke-width="2.5" stroke-dasharray="22 14"/>
    <polygon class="flag-band" points="530,850 1200,110 1200,850" fill="var(--white)"/>
    <polygon class="flag-stripe" points="600,850 1200,190 1200,240 650,850" fill="var(--flag-red)"/>
    <polygon class="flag-stripe" points="720,850 1200,320 1200,370 770,850" fill="var(--flag-red)"/>
    <rect class="eagle-illustration" role="img" aria-label="Illustration of a screeching bald eagle with spread wings"
          x="690" y="0" width="510" height="850" fill="url(#eagleTone)"/>
  </svg>

  <h1 class="greeting greeting--thanks">Thank You</h1>
  <div class="star-row star-row--top" aria-hidden="true">
    <svg viewBox="0 0 24 24"><polygon points="12,1 15,9 23,9 16.5,14 19,22 12,17 5,22 7.5,14 1,9 9,9"/></svg>
    <svg viewBox="0 0 24 24"><polygon points="12,1 15,9 23,9 16.5,14 19,22 12,17 5,22 7.5,14 1,9 9,9"/></svg>
    <svg viewBox="0 0 24 24"><polygon points="12,1 15,9 23,9 16.5,14 19,22 12,17 5,22 7.5,14 1,9 9,9"/></svg>
  </div>
  <p class="greeting greeting--for">For Being</p>
  <p class="greeting greeting--great">a Great</p>
  <p class="greeting greeting--american">American</p>
  <div class="star-row star-row--bottom" aria-hidden="true">
    <svg viewBox="0 0 24 24"><polygon points="12,1 15,9 23,9 16.5,14 19,22 12,17 5,22 7.5,14 1,9 9,9"/></svg>
    <svg viewBox="0 0 24 24"><polygon points="12,1 15,9 23,9 16.5,14 19,22 12,17 5,22 7.5,14 1,9 9,9"/></svg>
    <svg viewBox="0 0 24 24"><polygon points="12,1 15,9 23,9 16.5,14 19,22 12,17 5,22 7.5,14 1,9 9,9"/></svg>
  </div>
</main>
</body>
</html>
```